Recruitment Agency Needs a Core Values Wall for Office

Hello! We are hoping to reach out to the designer community to help us with achieving a wall in our office that beautifully presents our core values, so thanks for stopping by!
We are in a corporate office, but our median age in the office is 28 years old. For this reason we want the design to be fun, young and colourful while showing some sophistication.
The wall will be visible to the staff (within the open plan office), and the right colours will need to be used to enhance mood and productivity. Perhaps we could be looking at a colour for each core value? Or potentially some other way for each value to stand out?
The background doesn't have to be a specific colour. We would like some options to see how it will reflect in the office.
In terms of size - we aren't 100% on what size we are wanting to do it... but work within 1500x2700mm and we can work off that.
Fonts can be experimented with, without being too overpowering to the eye.
It needs to be clear, punchy and stand out from across the office (while being easy on the eye).
I have attached two images that can be used as inspiration. We would like more colour throughout the design.
The core values that will be required to be displayed:
Stop. Think. Challenge the Norm.
Our Detail is Our Difference.
Best Intentions. ALWAYS.
Turn Up, Turn On! Make ..it Happen!
Support Like Family. Party Like Rockstars.
Median staff age of 28, corporate office
Recruitment

```html
<!DOCTYPE html>
<html lang="en">
<head>
<meta charset="utf-8">
<title>Core Values Wall</title>
<link rel="stylesheet" href="https://fonts.googleapis.com/css2?family=Roboto+Slab:wght@300;400;800;900&family=Oswald:wght@400;500&family=Orbitron:wght@700&family=Rubik+Mono+One&display=swap">
<style>
  :root {
    --paper: #ebebeb;
    --paper-shade: #dedede;
    --ink: #231f20;
    --rule: #2b2b2b;
    --red: #e8333c;
    --cyan: #1aa7e0;
    --navy: #3a3f8f;
    --green: #0aa14b;
    --orange: #f28a30;
    --grey: #58595b;
    --magenta: #b3318f;
  }
  html, body {
    margin: 0;
    padding: 0;
    width: 821px;
    height: 1200px;
    overflow: hidden;
    background: var(--paper);
  }
  .values-wall {
    display: block;
    width: 821px;
    height: 1200px;
    background: linear-gradient(180deg, var(--paper) 0%, var(--paper-shade) 100%);
  }
  .rule { stroke: var(--rule); stroke-width: 3; stroke-linecap: round; }
  .slab-bold { font-family: "Roboto Slab", Georgia, serif; font-weight: 900; }
  .slab-light { font-family: "Roboto Slab", Georgia, serif; font-weight: 300; }
  .condensed { font-family: "Oswald", "Arial Narrow", sans-serif; font-weight: 400; }
  .condensed-strong { font-family: "Oswald", "Arial Narrow", sans-serif; font-weight: 500; }
  .outline-caps {
    font-family: "Orbitron", Arial, sans-serif;
    font-weight: 700;
    fill: none;
    stroke: var(--navy);
    stroke-width: 2;
  }
  .marquee { font-family: "Rubik Mono One", Impact, sans-serif; fill: var(--magenta); }
  .value-stop { fill: var(--red); }
  .value-think { fill: var(--cyan); }
  .value-norm { fill: var(--navy); }
  .value-detail { fill: var(--green); }
  .value-difference { fill: var(--orange); }
  .value-intentions { fill: var(--grey); }
  .value-turn-up { fill: var(--red); }
  .value-turn-on { fill: var(--green); }
  .value-happen { fill: var(--navy); }
  .icon-fill { fill: var(--ink); }
  .ornament-fill { fill: var(--grey); opacity: 0.55; }
</style>
</head>
<body>
<svg class="values-wall" viewBox="0 0 800 1169" width="821" height="1200" xmlns="http://www.w3.org/2000/svg">

  <!-- Value 1 -->
  <line class="rule" x1="112" y1="90" x2="678" y2="90"/>
  <text class="slab-bold value-stop" x="130" y="164" font-size="70" textLength="230" lengthAdjust="spacingAndGlyphs">STOP.</text>
  <text class="slab-bold value-think" x="380" y="164" font-size="70" textLength="292" lengthAdjust="spacingAndGlyphs">THINK.</text>
  <text class="slab-light value-norm" x="120" y="208" font-size="37" textLength="560" lengthAdjust="spacingAndGlyphs">CHALLENGE THE NORM.</text>

  <line class="rule" x1="112" y1="230" x2="362" y2="230"/>
  <rect class="icon-fill" x="374" y="215" width="28" height="28" rx="5" role="img" aria-label="Thumbs-up hand icon"/>
  <line class="rule" x1="414" y1="230" x2="678" y2="230"/>

  <!-- Value 2 -->
  <text class="slab-light value-detail" x="115" y="316" font-size="82" textLength="195" lengthAdjust="spacingAndGlyphs">OUR</text>
  <text class="slab-light value-detail" x="115" y="355" font-size="30" textLength="195" lengthAdjust="spacingAndGlyphs">DETAIL IS</text>
  <text class="slab-bold value-difference" x="328" y="360" font-size="150" textLength="352" lengthAdjust="spacingAndGlyphs">OUR</text>
  <text class="slab-bold value-difference" x="117" y="430" font-size="82" textLength="573" lengthAdjust="spacingAndGlyphs">DIFFERENCE.</text>

  <line class="rule" x1="112" y1="452" x2="350" y2="452"/>
  <rect class="icon-fill" x="362" y="444" width="72" height="18" rx="6" role="img" aria-label="Pointing hand icon"/>
  <line class="rule" x1="446" y1="452" x2="678" y2="452"/>

  <!-- Value 3 -->
  <rect class="ornament-fill" x="55" y="500" width="55" height="22" rx="11" role="img" aria-label="Curled flourish ornament"/>
  <text class="condensed value-intentions" x="118" y="540" font-size="76" textLength="572" lengthAdjust="spacingAndGlyphs">BEST INTENTIONS. ALWAYS.</text>
  <rect class="ornament-fill" x="698" y="500" width="55" height="22" rx="11" role="img" aria-label="Curled flourish ornament"/>

  <!-- Value 4 -->
  <text class="slab-light value-turn-up" x="120" y="602" font-size="48" textLength="250" lengthAdjust="spacingAndGlyphs">TURN UP,</text>
  <text class="slab-bold value-turn-on" x="385" y="602" font-size="48" textLength="315" lengthAdjust="spacingAndGlyphs">TURN ON!</text>
  <text class="condensed-strong value-happen" x="120" y="703" font-size="104" textLength="578" lengthAdjust="spacingAndGlyphs">MAKE ..IT HAPPEN!</text>

  <line class="rule" x1="118" y1="748" x2="330" y2="748"/>
  <circle class="icon-fill" cx="383" cy="745" r="28" role="img" aria-label="Smiley icon"/>
  <line class="rule" x1="438" y1="748" x2="690" y2="748"/>

  <!-- Value 5 -->
  <text class="outline-caps" x="118" y="820" font-size="34" textLength="595" lengthAdjust="spacingAndGlyphs">SUPPORT LIKE FAMILY.</text>
  <text class="marquee" x="118" y="922" font-size="88" textLength="572" lengthAdjust="spacingAndGlyphs">PARTY LIKE</text>

  <line class="rule" x1="122" y1="962" x2="352" y2="962"/>
  <rect class="icon-fill" x="364" y="934" width="56" height="48" rx="8" role="img" aria-label="Silhouette of a rock fan with raised hand"/>
  <line class="rule" x1="432" y1="962" x2="690" y2="962"/>

  <text class="marquee" x="118" y="1056" font-size="80" textLength="592" lengthAdjust="spacingAndGlyphs">ROCKSTARS.</text>
  <line class="rule" x1="118" y1="1075" x2="690" y2="1075"/>
</svg>
</body>
</html>
```